Hollow Meridian Book website design.

This is a simple one-page web design for my book.
I have all files and video needed.
Domain listed with Net Harbor.
Password and username will be given to winning bid.
Domain address, www.hollowmeridian.info
Upload a 30 second video so it can be played on the website.
Book cover photo
Book Blurb text.
Links to Rivermart and Audio books where the book can be purchased.
Below is the link to the Rivermart listing.
https://www.rivermart.example/dp/X00AAAAAA1/?coliid=QWERTYUIOPASD&colid=1ZXCVBNMLKJH0&psc=0&ref_=lv_ov_lig_dp_i
Below is the link to my Listenly books.com listing.
https://www.listenly.example/pd/Hollow-Meridian-Audiobook/X00BBBBBB2?qid=1000000001&sr=1-7&ref=a_search_c3_lProduct_1_7&pf_rd_p=00000000-aaaa-bbbb-cccc-000000000000&pf_rd_r=ZZZZ00000000000000QQ
Text on page.” Click on either logo to go directly to Rivermart or Listenly.com
Link Listenly book logo to my book on Listenly.com
Place this text under Listenly.com logo: “Free to new members of Listenly.com”
Link Rivermart logo to my book on Rivermart.
Place this text under Rivermart logo “ Free to new Pagewisp members on Rivermart.com”
Link the book photo to the Rivermart.com web address as well.
Enter meta tags or keywords below for search engines to locate webpage.
Hollow Meridian
Conspiracy
Conspiracy Books
Spy books
Thriller books
Suspense books
Comedy books
Dorian Welbeck

```html
<!DOCTYPE html>
<html lang="en">
<head>
<meta charset="utf-8">
<title>Hollow Meridian — a novel by Dorian Welbeck</title>
<meta name="keywords" content="Hollow Meridian, Conspiracy, Conspiracy Books, Spy books, Thriller books, Suspense books, Comedy books, Dorian Welbeck">
<link rel="stylesheet" href="https://fonts.googleapis.com/css2?family=Abril+Fatface&family=Playfair+Display:wght@400&family=Poppins:wght@600&family=Mulish:wght@400;600;700&family=Roboto:wght@400&display=swap">
<style>
  :root {
    --navy-deep: #081a30;
    --navy-mid: #0f3042;
    --teal-haze: #1c4a4a;
    --amber-glow: #8a561c;
    --accent-orange: #e8461f;
    --play-red: #e8333b;
    --frame: #2c3a42;
    --panel-left: #f0f0f0;
    --panel-right: #e2e3e7;
    --ink: #1d1f24;
    --ink-soft: #34373d;
    --button-navy: #0e3b79;
    --footer: #1c1c1d;
    --footer-text: #e2e2e2;
    --white: #ffffff;
  }
  * { margin: 0; padding: 0; box-sizing: border-box; }
  html, body { width: 1170px; height: 1200px; overflow: hidden; }
  body { position: relative; background: var(--panel-left); font-family: "Mulish", sans-serif; color: var(--ink); }

  .hero {
    position: absolute; left: 0; top: 0; width: 1170px; height: 659px; overflow: hidden;
    background:
      radial-gradient(ellipse 420px 300px at 1000px 620px, rgba(160,100,30,0.75), transparent 70%),
      radial-gradient(ellipse 500px 260px at 580px 330px, rgba(60,90,60,0.55), transparent 75%),
      radial-gradient(ellipse 400px 260px at 120px 600px, rgba(10,14,20,0.9), transparent 70%),
      linear-gradient(180deg, var(--navy-deep) 0%, var(--navy-mid) 35%, var(--teal-haze) 60%, #1a2226 100%);
  }
  .hero__title {
    position: absolute; top: 34px; left: 0; width: 100%; text-align: center;
    font-family: "Abril Fatface", serif; font-size: 38px; color: var(--white); font-weight: 400;
  }
  .hero__tagline {
    position: absolute; top: 104px; left: 0; width: 100%; text-align: center;
    font-family: "Playfair Display", serif; font-size: 31px; line-height: 40px; color: var(--white); font-weight: 400;
  }
  .watch-button {
    position: absolute; left: 498px; top: 223px; width: 174px; height: 44px;
    border-radius: 22px; background: var(--accent-orange); color: var(--white);
    display: flex; align-items: center; justify-content: center; gap: 9px;
    font-family: "Poppins", sans-serif; font-weight: 600; font-size: 16px; text-decoration: none;
  }
  .flag-band { position: absolute; top: 492px; width: 277px; height: 167px; }
  .flag-band--left { left: 0; }
  .flag-band--right { left: 893px; }
  .video-frame {
    position: absolute; left: 267px; top: 305px; width: 636px; height: 354px;
    background: var(--frame); padding: 10px 10px 0 10px;
  }
  .video-still {
    width: 616px; height: 344px;
    background:
      radial-gradient(ellipse 200px 220px at 420px 170px, rgba(120,100,95,0.55), transparent 70%),
      radial-gradient(ellipse 160px 140px at 160px 120px, rgba(70,110,140,0.45), transparent 70%),
      linear-gradient(160deg, #1c2532 0%, #222a33 45%, #3b3a40 100%);
  }
  .play-button { position: absolute; left: 549px; top: 457px; }

  .offer { position: absolute; top: 659px; height: 472px; }
  .offer--ebook { left: 0; width: 589px; background: var(--panel-left); }
  .offer--audio { left: 589px; width: 581px; background: var(--panel-right); }
  .book-cover { position: absolute; display: block; }
  .book-cover--ebook {
    left: 37px; top: 57px; width: 178px; height: 258px; border-radius: 3px 6px 6px 3px;
    background: linear-gradient(150deg, #1e2a52 0%, #5a1a22 45%, #1b1b1f 75%, #2b2b2e 100%);
    box-shadow: -8px 14px 22px rgba(0,0,0,0.3);
  }
  .book-cover--audio {
    left: 25px; top: 58px; width: 205px; height: 240px;
    background: linear-gradient(180deg, #000 0%, #000 50%, #2a2a2a 75%, #111 100%);
  }
  .offer__body { position: absolute; top: 50px; width: 300px; }
  .offer--ebook .offer__body { left: 250px; }
  .offer--audio .offer__body { left: 253px; top: 53px; }
  .offer__title { font-size: 19.5px; line-height: 23px; font-weight: 600; color: var(--ink); }
  .offer__perk { margin-top: 15px; font-size: 12.5px; font-weight: 600; color: var(--ink); }
  .offer--audio .offer__perk { margin-top: 16px; }
  .store-name {
    display: inline-block; margin-top: 6px; font-size: 22px; font-weight: 700; color: var(--ink);
    text-decoration: none; letter-spacing: -0.3px;
  }
  .offer__blurb { margin-top: 21px; width: 292px; font-size: 12.4px; line-height: 17.2px; font-weight: 400; color: var(--ink-soft); }
  .offer--audio .offer__blurb { margin-top: 33px; }
  .store-button {
    position: absolute; top: 378px; height: 36px; border-radius: 18px;
    background: var(--button-navy); color: var(--white); text-decoration: none;
    display: flex; align-items: center; justify-content: center; gap: 8px;
    font-size: 12.8px; font-weight: 600;
  }
  .offer--ebook .store-button { left: 250px; width: 248px; }
  .offer--audio .store-button { left: 253px; width: 254px; }

  .site-footer {
    position: absolute; left: 0; top: 1131px; width: 1170px; height: 69px; background: var(--footer);
    display: flex; align-items: center; justify-content: center;
    font-family: "Roboto", sans-serif; font-size: 13px; color: var(--footer-text);
  }
</style>
</head>
<body>
  <header class="hero">
    <h1 class="hero__title">Hollow Meridian</h1>
    <p class="hero__tagline">A fictional novel based on current events<br>surrounding the covid 19 virous.</p>
    <a class="watch-button" href="#trailer">
      <svg width="26" height="26" viewBox="0 0 26 26" aria-hidden="true"><circle cx="13" cy="13" r="11" fill="none" stroke="#fff" stroke-width="2.2"/><path d="M10.5 8.5 L17.5 13 L10.5 17.5 Z" fill="#fff"/></svg>
      Watch Video
    </a>
    <svg class="flag-band flag-band--left" viewBox="0 0 277 167" role="img" aria-label="Waving American flag decoration">
      <defs>
        <linearGradient id="flagFadeL" x1="0" y1="0" x2="0" y2="1">
          <stop offset="0" stop-color="#d8dbe6" stop-opacity="0"/>
          <stop offset="0.35" stop-color="#c9cfe0" stop-opacity="0.7"/>
          <stop offset="0.7" stop-color="#e6e6ea"/>
          <stop offset="1" stop-color="#d4303a"/>
        </linearGradient>
      </defs>
      <rect width="277" height="167" fill="url(#flagFadeL)"/>
    </svg>
    <svg class="flag-band flag-band--right" viewBox="0 0 277 167" role="img" aria-label="Waving American flag decoration">
      <defs>
        <linearGradient id="flagFadeR" x1="0" y1="0" x2="0" y2="1">
          <stop offset="0" stop-color="#d8dbe6" stop-opacity="0"/>
          <stop offset="0.35" stop-color="#c9cfe0" stop-opacity="0.7"/>
          <stop offset="0.7" stop-color="#e6e6ea"/>
          <stop offset="1" stop-color="#d4303a"/>
        </linearGradient>
      </defs>
      <rect width="277" height="167" fill="url(#flagFadeR)"/>
    </svg>
    <div class="video-frame" id="trailer">
      <div class="video-still" role="img" aria-label="Book trailer video still: a journalist seated in a dim room with glowing screens"></div>
    </div>
    <svg class="play-button" width="70" height="70" viewBox="0 0 70 70" aria-label="Play video" role="img">
      <circle cx="35" cy="35" r="35" fill="var(--play-red)"/>
      <path d="M26 20 L52 35 L26 50 Z" fill="#fff"/>
    </svg>
  </header>

  <main>
    <section class="offer offer--ebook">
      <a class="book-cover book-cover--ebook" href="https://www.rivermart.example/dp/X00AAAAAA1/?coliid=QWERTYUIOPASD&amp;colid=1ZXCVBNMLKJH0&amp;psc=0&amp;ref_=lv_ov_lig_dp_i" role="img" aria-label="Hardcover book of Hollow Meridian by Dorian Welbeck, flag and profile cover art"></a>
      <div class="offer__body">
        <h2 class="offer__title">Hollow Meridian<br>Pagewisp Edition</h2>
        <p class="offer__perk">Free to new Pagewisp members on Rivermart.com</p>
        <a class="store-name" href="https://www.rivermart.example/dp/X00AAAAAA1/?coliid=QWERTYUIOPASD&amp;colid=1ZXCVBNMLKJH0&amp;psc=0&amp;ref_=lv_ov_lig_dp_i">Rivermart</a>
        <p class="offer__blurb">A fictional novel based on current events surrounding the covid 19 virous. Evan Marlowe is a well-respected independent journalist contracted by the Harbor City Ledger, upon his return from reporting on the war in Syria he is tasked to investigate the covid virus outbreak in China. As he digs deeper, he uncovers a hideous plot by the powers that be here in America. Evan risks life and limb to uncover the conspirers behind all of this and shed light to the American people.</p>
      </div>
      <a class="store-button" href="https://www.rivermart.example/dp/X00AAAAAA1/?coliid=QWERTYUIOPASD&amp;colid=1ZXCVBNMLKJH0&amp;psc=0&amp;ref_=lv_ov_lig_dp_i">
        <svg width="14" height="14" viewBox="0 0 14 14" aria-hidden="true"><circle cx="7" cy="7" r="6" fill="#fff"/></svg>
        Click to go directly to Rivermart.com
      </a>
    </section>

    <section class="offer offer--audio">
      <a class="book-cover book-cover--audio" href="https://www.listenly.example/pd/Hollow-Meridian-Audiobook/X00BBBBBB2?qid=1000000001&amp;sr=1-7&amp;ref=a_search_c3_lProduct_1_7&amp;pf_rd_p=00000000-aaaa-bbbb-cccc-000000000000&amp;pf_rd_r=ZZZZ00000000000000QQ" role="img" aria-label="Audiobook cover of Hollow Meridian by Dorian Welbeck, black cover with title and profile portrait"></a>
      <div class="offer__body">
        <h2 class="offer__title">Hollow Meridian</h2>
        <p class="offer__perk">Free to new members of Listenly.com</p>
        <a class="store-name" href="https://www.listenly.example/pd/Hollow-Meridian-Audiobook/X00BBBBBB2?qid=1000000001&amp;sr=1-7&amp;ref=a_search_c3_lProduct_1_7&amp;pf_rd_p=00000000-aaaa-bbbb-cccc-000000000000&amp;pf_rd_r=ZZZZ00000000000000QQ">Listenly</a>
        <p class="offer__blurb">A fictional novel based on current events surrounding the covid 19 virous. Evan Marlowe is a well-respected independent journalist contracted by the Harbor City Ledger, upon his return from reporting on the war in Syria he is tasked to investigate the covid virus outbreak in China. As he digs deeper, he uncovers a hideous plot by the powers that be here in America. Evan risks life and limb to uncover the conspirers behind all of this and shed light to the American people.</p>
      </div>
      <a class="store-button" href="https://www.listenly.example/pd/Hollow-Meridian-Audiobook/X00BBBBBB2?qid=1000000001&amp;sr=1-7&amp;ref=a_search_c3_lProduct_1_7&amp;pf_rd_p=00000000-aaaa-bbbb-cccc-000000000000&amp;pf_rd_r=ZZZZ00000000000000QQ">
        <svg width="14" height="14" viewBox="0 0 14 14" aria-hidden="true"><circle cx="7" cy="7" r="6" fill="#fff"/></svg>
        Click to go directly to Listenly.com
      </a>
    </section>
  </main>

  <footer class="site-footer">Copyright © 2022 All Rights Reserved</footer>
</body>
</html>
```